Business Card Design for company

We want new business cards. We'd like something different-- yet still highly professional. Our tagline is Providing leadership, delivering success. Stock photos are ok, as long as they are relevant and look upscale.

Target Market(s)

Architecture/Business Management Consulting/Engineering Consulting

Contact Information for Business Card

dark gray background with pops of blue might be good, but you tell me. You're the designers. Rounded corners might be nice, but again, you tell me.

Font styles to use
Serif
Sans Serif

Colors
3276b5
5c5c5c
9d9d9d
fbfbfb

Requirements
Nice to have
• Something different, but still very professional.

```html
<!DOCTYPE html>
<html lang="en">
<head>
<meta charset="utf-8">
<title>Veltran Group — Business Card</title>
<link rel="stylesheet" href="https://fonts.googleapis.com/css2?family=Open+Sans:wght@400;600;700&display=swap">
<style>
  :root {
    --bg: #4a423e;
    --card: #1f2226;
    --blue: #3276b5;
    --silver: #d9d9d9;
    --grey: #9d9d9d;
    --white: #fbfbfb;
  }
  * { box-sizing: border-box; margin: 0; padding: 0; }
  html, body { width: 1200px; height: 864px; overflow: hidden; }
  body {
    background: var(--bg);
    font-family: "Open Sans", sans-serif;
    position: relative;
  }
  .card {
    position: absolute;
    left: 300px;
    width: 600px;
    height: 343px;
    background: var(--card);
    border-radius: 4px;
    box-shadow: 0 10px 24px rgba(0,0,0,0.35);
  }
  .card-front { top: 60px; }
  .card-back { top: 461px; }

  .brand { display: flex; flex-direction: column; line-height: 1; font-weight: 600; }
  .brand-main { font-size: 58px; letter-spacing: 2px; }
  .brand-sub { font-size: 20px; letter-spacing: 7px; margin-top: 8px; }

  .card-front .brand {
    position: absolute; left: 150px; top: 92px; color: var(--silver);
  }
  .tagline {
    position: absolute; left: 150px; top: 222px;
    color: var(--white); font-size: 15px; letter-spacing: 0.3px;
    white-space: nowrap;
  }
  .tagline .dot {
    display: inline-block; width: 6px; height: 6px; border-radius: 50%;
    background: var(--white); vertical-align: middle; margin: 0 8px;
  }

  .card-back .brand {
    position: absolute; left: 40px; top: 118px; color: var(--blue);
  }
  .card-back .brand-main { font-size: 50px; }
  .card-back .brand-sub { font-size: 17px; letter-spacing: 6px; }
  .divider {
    position: absolute; left: 318px; top: 60px; width: 1px; height: 230px;
    background: linear-gradient(to bottom, transparent, var(--grey) 20%, var(--white) 50%, var(--grey) 80%, transparent);
  }
  .contact {
    position: absolute; left: 340px; top: 70px; color: var(--white);
    font-size: 14px; line-height: 1.35;
  }
  .contact-name { color: var(--blue); font-weight: 700; font-size: 19px; letter-spacing: 0.5px; }
  .contact-title { font-size: 14px; letter-spacing: 0.5px; margin-bottom: 8px; }
  .contact-address { margin-bottom: 6px; }
  .contact-list { list-style: none; }
  .contact-list li { display: flex; align-items: center; gap: 9px; height: 21px; white-space: nowrap; }
  .contact-list svg { width: 13px; height: 13px; fill: var(--blue); flex: none; }
</style>
</head>
<body>
  <section class="card card-front">
    <div class="brand">
      <span class="brand-main">VELTRAN</span>
      <span class="brand-sub">GROUP</span>
    </div>
    <p class="tagline">Guiding strategy<span class="dot"></span>building results</p>
  </section>

  <section class="card card-back">
    <div class="brand">
      <span class="brand-main">VELTRAN</span>
      <span class="brand-sub">GROUP</span>
    </div>
    <div class="divider"></div>
    <div class="contact">
      <p class="contact-name">DANIEL FERRO</p>
      <p class="contact-title">PRESIDENT</p>
      <p class="contact-address">2710 Harrow Lane<br>Maple Ridge, NY 11020</p>
      <ul class="contact-list">
        <li><svg viewBox="0 0 16 16" aria-hidden="true"><path d="M3 2h3l1.5 3.5-2 1.2a8 8 0 0 0 3.8 3.8l1.2-2L14 10v3a1 1 0 0 1-1 1A11 11 0 0 1 2 3a1 1 0 0 1 1-1z"/></svg>555 0142 7731</li>
        <li><svg viewBox="0 0 16 16" aria-hidden="true"><path d="M4.5 1h7a1 1 0 0 1 1 1v12a1 1 0 0 1-1 1h-7a1 1 0 0 1-1-1V2a1 1 0 0 1 1-1zm1 2v9h5V3z"/></svg>555 0187 2264</li>
        <li><svg viewBox="0 0 16 16" aria-hidden="true"><path d="M4 1h6l2 2v3H4zM2 7h12v7H2zm2 2v1h3V9z"/></svg>555 0163 9418</li>
        <li><svg viewBox="0 0 16 16" aria-hidden="true"><path d="M1 3h14v10H1zm1.5 1.5L8 9l5.5-4.5z"/></svg>daniel@veltrangroup.com</li>
        <li><svg viewBox="0 0 16 16" aria-hidden="true"><circle cx="8" cy="8" r="7"/></svg>www.veltrangroup.com</li>
      </ul>
    </div>
  </section>
</body>
</html>
```